New design for sprouting seed packaging.

We need a new design for our consumer packaging. The basic range we are starting with is 6 bags, 3 seed mixes and 3 single seed bags, we want a basic design that we can then change a little in colors and seed images so that we achieve all different varieties.
We want the design to be timeless and calm. We only work with organic seeds and in Europe KR-VAMI. We are attaching some images that we have developed to give a taste of our profile, but we want you to find a new way forward with this brand, so that the packaging becomes unique for Lundovia Hearth Plot. If you want to reuse something, that's fine too. Also attaching a picture of the older bags with the label that was stuck on and the base for the two different sizes we will use. A company that works with colors on their packaging is www.kavelbrim.com, a colleague in the US that has been around for a long time. Maybe you can take inspiration from this link. If you need any more information about this project, just get in touch. The two original files for creating the bag are: 120x170x60mm and 130x202x80mm

Target Market(s)

Consumers interested in farming and healthy lifestyles

Requirements
Nice to have
• At the top of the bag where you tear off in light gray text, not so prominently, you could have the text: (Frön + Vatten + Några dagar = Bra mat!), Which means "Seeds + Water + A Few Days = Great Food!"

```html
<!DOCTYPE html>
<html lang="sv">
<head>
<meta charset="utf-8">
<title>Lundovia Hearth Plot – groddfrön, förpackningsserie</title>
<link rel="stylesheet" href="https://fonts.googleapis.com/css2?family=Oswald:wght@500&family=Open+Sans:wght@400;600;700&display=swap">
<style>
  :root{
    --paper:#ffffff;
    --foil-top:#f6f6f6;
    --foil-bottom:#e4e4e4;
    --ink:#2f3a2c;
    --logo:#2d4f2a;
    --tagline:#8b8b8b;
    --alfalfa:#b0864f;
    --vardag:#3fae49;
    --broccoli:#9b2a8e;
    --mung:#c8202e;
    --sallad:#d18a2c;
    --art:#1f7cc4;
    --organic:#4f9a2e;
  }
  *{box-sizing:border-box;margin:0;padding:0}
  html,body{width:1200px;height:1200px;overflow:hidden;background:var(--paper)}
  body{position:relative;font-family:"Open Sans",sans-serif;color:var(--ink)}

  .range-row{position:absolute;left:0;width:1200px;height:340px}
  .row-alfalfa{top:106px}
  .row-broccoli{top:472px}
  .row-sallad{top:834px}

  /* bottom swatches */
  .bottom-swatch{position:absolute;display:flex;align-items:center;justify-content:center;background:var(--c)}
  .bottom-swatch.left{left:62px;top:128px;width:154px;height:77px}
  .bottom-swatch.right{left:973px;top:103px;width:177px;height:108px}
  .swatch-name{font-weight:700;font-size:11px;color:#fff;letter-spacing:.2px}
  .swatch-caption{position:absolute;top:216px;font-size:12.5px;line-height:15px;text-align:center;color:#222}
  .swatch-caption.left{left:40px;width:198px}
  .swatch-caption.right{left:961px;width:201px}

  /* bags */
  .bag{position:absolute;overflow:hidden;border-radius:7px 7px 5px 5px;
       background:linear-gradient(180deg,var(--foil-top),var(--foil-bottom));
       box-shadow:0 1px 3px rgba(0,0,0,.12)}
  .bag.small{top:36px;width:165px;height:232px;--s:1}
  .bag.large{top:0;width:181px;height:270px;--s:1.12}
  .bag.pos1{left:242px}.bag.pos2{left:412px}.bag.pos3{left:583px}.bag.pos4{left:767px}
  .bag-color{position:absolute;inset:0;width:100%;height:100%;fill:var(--c)}
  .zipper{position:absolute;left:6%;right:6%;top:6.5%;height:1px;background:#d2d2d2}
  .tagline{position:absolute;left:0;right:0;top:9.5%;text-align:center;font-size:calc(5px*var(--s));color:var(--tagline);font-weight:600;letter-spacing:.2px}

  .front .brand{position:absolute;left:0;right:0;top:21%;text-align:center;font-weight:700;font-size:calc(12px*var(--s));color:var(--logo)}
  .front .kind{position:absolute;left:0;right:0;top:44%;text-align:center;font-size:calc(4.6px*var(--s));color:#fff;font-weight:600;letter-spacing:.3px}
  .front .title{position:absolute;left:0;right:0;top:48%;text-align:center;font-family:"Oswald",sans-serif;font-weight:500;font-size:calc(16px*var(--s));color:#fff;letter-spacing:.4px}
  .front .title.long{font-size:calc(14px*var(--s))}
  .front .variety{position:absolute;left:10%;right:10%;top:58%;text-align:center;font-size:calc(4.2px*var(--s));line-height:1.3;color:#fff;font-weight:600;letter-spacing:.6px}
  .front .sprout-photo{position:absolute;left:8%;right:0;top:64%;bottom:0;border-radius:70% 0 0 0;background:var(--seed)}
  .front .seal{position:absolute;right:8%;top:57%;width:calc(22px*var(--s));height:calc(22px*var(--s));border-radius:50%;background:#efe9dc;border:1px solid #c9bfa6}
  .organic{position:absolute;width:calc(14px*var(--s));height:calc(10px*var(--s));background:var(--organic)}
  .front .organic{left:11%;bottom:9%}
  .cert-code{position:absolute;font-size:calc(3px*var(--s));color:#fff;line-height:1.2}
  .front .cert-code{left:8%;bottom:3.5%}
  .weight{position:absolute;border-radius:50%;border:1.5px solid #fff;background:var(--c);color:#fff;display:flex;flex-direction:column;align-items:center;justify-content:center;font-weight:700;width:calc(19px*var(--s));height:calc(19px*var(--s));font-size:calc(4.6px*var(--s));line-height:1}
  .weight small{font-size:calc(2.4px*var(--s));font-weight:400;margin-top:1px}
  .front .weight{right:8%;bottom:7%}

  .back .brand{position:absolute;left:0;right:0;top:15.5%;text-align:center;font-weight:700;font-size:calc(8px*var(--s));color:var(--logo)}
  .back .copy{position:absolute;left:9%;top:34%;width:54%;color:#fff;font-size:calc(3px*var(--s));line-height:1.35}
  .back .copy h3{font-size:calc(3.8px*var(--s));font-weight:700;margin-bottom:1px}
  .back .copy p{margin:0}
  .back .seed-photo{position:absolute;right:3%;top:31%;width:33%;height:30%;border-radius:45% 8% 8% 45%;background:var(--seed)}
  .back .weight{right:25%;top:62%}
  .back .organic{right:28%;top:72%}
  .back .cert-code{right:24%;top:77%}
  .back .info-box{position:absolute;left:58%;top:81%;width:32%;height:8.5%;background:#fff;border-radius:1px;padding:2px 3px;font-size:calc(2.6px*var(--s));line-height:1.3;color:#222}
  .back .info-box b{font-weight:700}
  .back .contact{position:absolute;left:9%;bottom:3.5%;width:80%;display:flex;gap:6%;color:#fff;font-size:calc(2.6px*var(--s));line-height:1.35}
  .back .contact p{margin:0}

  .alfalfa{--c:var(--alfalfa);--seed:radial-gradient(circle at 65% 55%,#c59b5a,#8a6634 70%,#5b4424)}
  .vardag{--c:var(--vardag);--seed:radial-gradient(circle at 65% 55%,#c4a873,#5b4a34 60%,#2e271f)}
  .broccoli{--c:var(--broccoli);--seed:radial-gradient(circle at 65% 55%,#6f4655,#3b2530 65%,#24161c)}
  .mung{--c:var(--mung);--seed:radial-gradient(circle at 65% 55%,#8a9a42,#56632a 65%,#343c19)}
  .sallad{--c:var(--sallad);--seed:radial-gradient(circle at 65% 55%,#c1925a,#6d4a2c 65%,#3c2818)}
  .art{--c:var(--art);--seed:radial-gradient(circle at 65% 55%,#d2b486,#8c6a45 65%,#4e3a25)}
</style>
</head>
<body>

<!-- ===== Alfalfa / Vardagsmix ===== -->
<section class="range-row row-alfalfa">
  <div class="bottom-swatch left alfalfa"><span class="swatch-name">Lundovia Hearth Plot</span></div>
  <p class="swatch-caption left">The bottom<br>of Alfalfa bag</p>

  <article class="bag small pos1 front alfalfa">
    <svg class="bag-color" viewBox="0 0 100 100" preserveAspectRatio="none" aria-hidden="true"><path d="M0 37 C28 33 55 41 100 34 L100 100 L0 100Z"/></svg>
    <div class="zipper"></div>
    <p class="tagline">Frön + Vatten + Några dagar = Bra mat!</p>
    <p class="brand">Lundovia Hearth Plot</p>
    <p class="kind">EKOLOGISKA GRODDFRÖN</p>
    <h2 class="title">ALFALFA</h2>
    <p class="variety">VERONI</p>
    <div class="seal"></div>
    <div class="sprout-photo" role="img" aria-label="Skål med alfalfagroddar och en hög alfalfafrön"></div>
    <div class="organic"></div>
    <p class="cert-code">SE-VAMI-03<br>KR-VAMI</p>
    <div class="weight">100 G<small>Nettovikt</small></div>
  </article>

  <article class="bag small pos2 back alfalfa">
    <svg class="bag-color" viewBox="0 0 100 100" preserveAspectRatio="none" aria-hidden="true"><path d="M0 24 C30 19 60 28 100 20 L100 100 L0 100Z"/></svg>
    <div class="zipper"></div>
    <p class="tagline">Frön + Vatten + Några dagar = Bra mat!</p>
    <p class="brand">Lundovia Hearth Plot</p>
    <div class="copy">
      <h3>Ekologiska Groddfrön, Alfalfa.</h3>
      <p>Ingredienser: alfalfa, broccoli, gröna ärtor, röda linser, mungbönor.</p>
      <p>Ursprungsland: Italien. Förvaring: torrt och svalt.</p>
      <p><b>Groddning i glasburk:</b></p>
      <p>1. Blötlägg fröna i 8–12 timmar.</p>
      <p>2. Skölj och låt rinna av.</p>
      <p>3. Skölj 2–3 gånger per dag.</p>
      <p>Skörda efter 3–5 dagar.</p>
    </div>
    <div class="seed-photo" role="img" aria-label="Närbild på alfalfafrön"></div>
    <div class="weight">100 G<small>Nettovikt</small></div>
    <div class="organic"></div>
    <p class="cert-code">SE-VAMI-03<br>KR-VAMI</p>
    <div class="info-box"><b>Bäst före</b>: 2026-05-25<br><b>Batch nr</b>: 20001-00005<br><b>Förpackningsdag</b>: 2024-08-01</div>
    <div class="contact">
      <div><p>hearthplot_garden</p><p>Lundovia Hearth Plot</p><p>hearthplot.se</p><p>info@hearthplot.se</p></div>
      <div><p>Lundovia Hearth Plot AB</p><p>Brunnsgatan 9</p><p>18610 Norrvik</p><p>Tel: 0701 234 567</p></div>
    </div>
  </article>

  <article class="bag large pos3 front vardag">
    <svg class="bag-color" viewBox="0 0 100 100" preserveAspectRatio="none" aria-hidden="true"><path d="M0 37 C28 33 55 41 100 34 L100 100 L0 100Z"/></svg>
    <div class="zipper"></div>
    <p class="tagline">Frön + Vatten + Några dagar = Bra mat!</p>
    <p class="brand">Lundovia Hearth Plot</p>
    <p class="kind">EKOLOGISKA GRODDFRÖN</p>
    <h2 class="title long">VARDAGSMIX</h2>
    <p class="variety">ALFALFA, BROCCOLI, GRÖNA ÄRTOR,<br>RÖDA LINSER, MUNGBÖNOR</p>
    <div class="seal"></div>
    <div class="sprout-photo" role="img" aria-label="Skål med blandade groddar och en hög blandade frön"></div>
    <div class="organic"></div>
    <p class="cert-code">SE-VAMI-03<br>KR-VAMI</p>
    <div class="weight">200 G<small>Nettovikt</small></div>
  </article>

  <article class="bag large pos4 back vardag">
    <svg class="bag-color" viewBox="0 0 100 100" preserveAspectRatio="none" aria-hidden="true"><path d="M0 24 C30 19 60 28 100 20 L100 100 L0 100Z"/></svg>
    <div class="zipper"></div>
    <p class="tagline">Frön + Vatten + Några dagar = Bra mat!</p>
    <p class="brand">Lundovia Hearth Plot</p>
    <div class="copy">
      <h3>Ekologiska Groddfrön, Vardagsmix.</h3>
      <p>Ingredienser: alfalfa, broccoli, gröna ärtor, röda linser, mungbönor.</p>
      <p>Ursprungsland: Italien. Förvaring: torrt och svalt.</p>
      <p><b>Groddning i glasburk:</b></p>
      <p>1. Blötlägg fröna i 8–12 timmar.</p>
      <p>2. Skölj och låt rinna av.</p>
      <p>3. Skölj 2–3 gånger per dag.</p>
      <p>Skörda efter 3–5 dagar.</p>
    </div>
    <div class="seed-photo" role="img" aria-label="Närbild på blandade frön"></div>
    <div class="weight">200 G<small>Nettovikt</small></div>
    <div class="organic"></div>
    <p class="cert-code">SE-VAMI-03<br>KR-VAMI</p>
    <div class="info-box"><b>Bäst före</b>: 2026-05-25<br><b>Batch nr</b>: 20001-00005<br><b>Förpackningsdag</b>: 2024-08-01</div>
    <div class="contact">
      <div><p>hearthplot_garden</p><p>Lundovia Hearth Plot</p><p>hearthplot.se</p><p>info@hearthplot.se</p></div>
      <div><p>Lundovia Hearth Plot AB</p><p>Brunnsgatan 9</p><p>18610 Norrvik</p><p>Tel: 0701 234 567</p></div>
    </div>
  </article>

  <div class="bottom-swatch right vardag"><span class="swatch-name">Lundovia Hearth Plot</span></div>
  <p class="swatch-caption right">The bottom<br>of Vardagsmix bag</p>
</section>

<!-- ===== Broccoli / Mungbönor ===== -->
<section class="range-row row-broccoli">
  <div class="bottom-swatch left broccoli"><span class="swatch-name">Lundovia Hearth Plot</span></div>
  <p class="swatch-caption left">The bottom<br>of Broccoli bag</p>

  <article class="bag small pos1 front broccoli">
    <svg class="bag-color" viewBox="0 0 100 100" preserveAspectRatio="none" aria-hidden="true"><path d="M0 37 C28 33 55 41 100 34 L100 100 L0 100Z"/></svg>
    <div class="zipper"></div>
    <p class="tagline">Frön + Vatten + Några dagar = Bra mat!</p>
    <p class="brand">Lundovia Hearth Plot</p>
    <p class="kind">EKOLOGISKA GRODDFRÖN</p>
    <h2 class="title">BROCCOLI</h2>
    <p class="variety">CALVENO</p>
    <div class="seal"></div>
    <div class="sprout-photo" role="img" aria-label="Skål med broccoligroddar och en hög broccolifrön"></div>
    <div class="organic"></div>
    <p class="cert-code">SE-VAMI-03<br>KR-VAMI</p>
    <div class="weight">100 G<small>Nettovikt</small></div>
  </article>

  <article class="bag small pos2 back broccoli">
    <svg class="bag-color" viewBox="0 0 100 100" preserveAspectRatio="none" aria-hidden="true"><path d="M0 24 C30 19 60 28 100 20 L100 100 L0 100Z"/></svg>
    <div class="zipper"></div>
    <p class="tagline">Frön + Vatten + Några dagar = Bra mat!</p>
    <p class="brand">Lundovia Hearth Plot</p>
    <div class="copy">
      <h3>Ekologiska Groddfrön, Broccoli.</h3>
      <p>Ingredienser: alfalfa, broccoli, gröna ärtor, röda linser, mungbönor.</p>
      <p>Ursprungsland: Italien. Förvaring: torrt och svalt.</p>
      <p><b>Groddning i glasburk:</b></p>
      <p>1. Blötlägg fröna i 8–12 timmar.</p>
      <p>2. Skölj och låt rinna av.</p>
      <p>3. Skölj 2–3 gånger per dag.</p>
      <p>Skörda efter 3–5 dagar.</p>
    </div>
    <div class="seed-photo" role="img" aria-label="Närbild på broccolifrön"></div>
    <div class="weight">100 G<small>Nettovikt</small></div>
    <div class="organic"></div>
    <p class="cert-code">SE-VAMI-03<br>KR-VAMI</p>
    <div class="info-box"><b>Bäst före</b>: 2026-05-25<br><b>Batch nr</b>: 20001-00005<br><b>Förpackningsdag</b>: 2024-08-01</div>
    <div class="contact">
      <div><p>hearthplot_garden</p><p>Lundovia Hearth Plot</p><p>hearthplot.se</p><p>info@hearthplot.se</p></div>
      <div><p>Lundovia Hearth Plot AB</p><p>Brunnsgatan 9</p><p>18610 Norrvik</p><p>Tel: 0701 234 567</p></div>
    </div>
  </article>

  <article class="bag large pos3 front mung">
    <svg class="bag-color" viewBox="0 0 100 100" preserveAspectRatio="none" aria-hidden="true"><path d="M0 37 C28 33 55 41 100 34 L100 100 L0 100Z"/></svg>
    <div class="zipper"></div>
    <p class="tagline">Frön + Vatten + Några dagar = Bra mat!</p>
    <p class="brand">Lundovia Hearth Plot</p>
    <p class="kind">EKOLOGISKA GRODDFRÖN</p>
    <h2 class="title long">MUNGBÖNOR</h2>
    <p class="variety">MARELLO</p>
    <div class="seal"></div>
    <div class="sprout-photo" role="img" aria-label="Skål med mungbönsgroddar och en hög mungbönor"></div>
    <div class="organic"></div>
    <p class="cert-code">SE-VAMI-03<br>KR-VAMI</p>
    <div class="weight">200 G<small>Nettovikt</small></div>
  </article>

  <article class="bag large pos4 back mung">
    <svg class="bag-color" viewBox="0 0 100 100" preserveAspectRatio="none" aria-hidden="true"><path d="M0 24 C30 19 60 28 100 20 L100 100 L0 100Z"/></svg>
    <div class="zipper"></div>
    <p class="tagline">Frön + Vatten + Några dagar = Bra mat!</p>
    <p class="brand">Lundovia Hearth Plot</p>
    <div class="copy">
      <h3>Ekologiska Groddfrön, Mungbönor.</h3>
      <p>Ingredienser: alfalfa, broccoli, gröna ärtor, röda linser, mungbönor.</p>
      <p>Ursprungsland: Italien. Förvaring: torrt och svalt.</p>
      <p><b>Groddning i glasburk:</b></p>
      <p>1. Blötlägg fröna i 8–12 timmar.</p>
      <p>2. Skölj och låt rinna av.</p>
      <p>3. Skölj 2–3 gånger per dag.</p>
      <p>Skörda efter 3–5 dagar.</p>
    </div>
    <div class="seed-photo" role="img" aria-label="Närbild på mungbönor"></div>
    <div class="weight">200 G<small>Nettovikt</small></div>
    <div class="organic"></div>
    <p class="cert-code">SE-VAMI-03<br>KR-VAMI</p>
    <div class="info-box"><b>Bäst före</b>: 2026-05-25<br><b>Batch nr</b>: 20001-00005<br><b>Förpackningsdag</b>: 2024-08-01</div>
    <div class="contact">
      <div><p>hearthplot_garden</p><p>Lundovia Hearth Plot</p><p>hearthplot.se</p><p>info@hearthplot.se</p></div>
      <div><p>Lundovia Hearth Plot AB</p><p>Brunnsgatan 9</p><p>18610 Norrvik</p><p>Tel: 0701 234 567</p></div>
    </div>
  </article>

  <div class="bottom-swatch right mung"><span class="swatch-name">Lundovia Hearth Plot</span></div>
  <p class="swatch-caption right">The bottom<br>of Mungbönor bag</p>
</section>

<!-- ===== Salladsmix / Ärt & Linsmix ===== -->
<section class="range-row row-sallad">
  <div class="bottom-swatch left sallad"><span class="swatch-name">Lundovia Hearth Plot</span></div>
  <p class="swatch-caption left">The bottom<br>of Salladsmix bag</p>

  <article class="bag small pos1 front sallad">
    <svg class="bag-color" viewBox="0 0 100 100" preserveAspectRatio="none" aria-hidden="true"><path d="M0 37 C28 33 55 41 100 34 L100 100 L0 100Z"/></svg>
    <div class="zipper"></div>
    <p class="tagline">Frön + Vatten + Några dagar = Bra mat!</p>
    <p class="brand">Lundovia Hearth Plot</p>
    <p class="kind">EKOLOGISKA GRODDFRÖN</p>
    <h2 class="title long">SALLADSMIX</h2>
    <p class="variety">ALFALFA, RÖD KLÖVER,<br>RÄDISA, BROCCOLI</p>
    <div class="seal"></div>
    <div class="sprout-photo" role="img" aria-label="Skål med salladsgroddar och en hög blandade frön"></div>
    <div class="organic"></div>
    <p class="cert-code">SE-VAMI-03<br>KR-VAMI</p>
    <div class="weight">100 G<small>Nettovikt</small></div>
  </article>

  <article class="bag small pos2 back sallad">
    <svg class="bag-color" viewBox="0 0 100 100" preserveAspectRatio="none" aria-hidden="true"><path d="M0 24 C30 19 60 28 100 20 L100 100 L0 100Z"/></svg>
    <div class="zipper"></div>
    <p class="tagline">Frön + Vatten + Några dagar = Bra mat!</p>
    <p class="brand">Lundovia Hearth Plot</p>
    <div class="copy">
      <h3>Ekologiska Groddfrön, Salladsmix.</h3>
      <p>Ingredienser: alfalfa, broccoli, gröna ärtor, röda linser, mungbönor.</p>
      <p>Ursprungsland: Italien. Förvaring: torrt och svalt.</p>
      <p><b>Groddning i glasburk:</b></p>
      <p>1. Blötlägg fröna i 8–12 timmar.</p>
      <p>2. Skölj och låt rinna av.</p>
      <p>3. Skölj 2–3 gånger per dag.</p>
      <p>Skörda efter 3–5 dagar.</p>
    </div>
    <div class="seed-photo" role="img" aria-label="Närbild på salladsmix-frön"></div>
    <div class="weight">100 G<small>Nettovikt</small></div>
    <div class="organic"></div>
    <p class="cert-code">SE-VAMI-03<br>KR-VAMI</p>
    <div class="info-box"><b>Bäst före</b>: 2026-05-25<br><b>Batch nr</b>: 20001-00005<br><b>Förpackningsdag</b>: 2024-08-01</div>
    <div class="contact">
      <div><p>hearthplot_garden</p><p>Lundovia Hearth Plot</p><p>hearthplot.se</p><p>info@hearthplot.se</p></div>
      <div><p>Lundovia Hearth Plot AB</p><p>Brunnsgatan 9</p><p>18610 Norrvik</p><p>Tel: 0701 234 567</p></div>
    </div>
  </article>

  <article class="bag large pos3 front art">
    <svg class="bag-color" viewBox="0 0 100 100" preserveAspectRatio="none" aria-hidden="true"><path d="M0 37 C28 33 55 41 100 34 L100 100 L0 100Z"/></svg>
    <div class="zipper"></div>
    <p class="tagline">Frön + Vatten + Några dagar = Bra mat!</p>
    <p class="brand">Lundovia Hearth Plot</p>
    <p class="kind">EKOLOGISKA GRODDFRÖN</p>
    <h2 class="title long">ÄRT &amp; LINSMIX</h2>
    <p class="variety">GRÖNA ÄRTOR, RÖDA LINSER,<br>GRÖNA LINSER, KIKÄRTOR</p>
    <div class="seal"></div>
    <div class="sprout-photo" role="img" aria-label="Skål med ärt- och linsgroddar och en hög ärtor och linser"></div>
    <div class="organic"></div>
    <p class="cert-code">SE-VAMI-03<br>KR-VAMI</p>
    <div class="weight">200 G<small>Nettovikt</small></div>
  </article>

  <article class="bag large pos4 back art">
    <svg class="bag-color" viewBox="0 0 100 100" preserveAspectRatio="none" aria-hidden="true"><path d="M0 24 C30 19 60 28 100 20 L100 100 L0 100Z"/></svg>
    <div class="zipper"></div>
    <p class="tagline">Frön + Vatten + Några dagar = Bra mat!</p>
    <p class="brand">Lundovia Hearth Plot</p>
    <div class="copy">
      <h3>Ekologiska Groddfrön, Ärt &amp; Linsmix.</h3>
      <p>Ingredienser: alfalfa, broccoli, gröna ärtor, röda linser, mungbönor.</p>
      <p>Ursprungsland: Italien. Förvaring: torrt och svalt.</p>
      <p><b>Groddning i glasburk:</b></p>
      <p>1. Blötlägg fröna i 8–12 timmar.</p>
      <p>2. Skölj och låt rinna av.</p>
      <p>3. Skölj 2–3 gånger per dag.</p>
      <p>Skörda efter 3–5 dagar.</p>
    </div>
    <div class="seed-photo" role="img" aria-label="Närbild på ärtor och linser"></div>
    <div class="weight">200 G<small>Nettovikt</small></div>
    <div class="organic"></div>
    <p class="cert-code">SE-VAMI-03<br>KR-VAMI</p>
    <div class="info-box"><b>Bäst före</b>: 2026-05-25<br><b>Batch nr</b>: 20001-00005<br><b>Förpackningsdag</b>: 2024-08-01</div>
    <div class="contact">
      <div><p>hearthplot_garden</p><p>Lundovia Hearth Plot</p><p>hearthplot.se</p><p>info@hearthplot.se</p></div>
      <div><p>Lundovia Hearth Plot AB</p><p>Brunnsgatan 9</p><p>18610 Norrvik</p><p>Tel: 0701 234 567</p></div>
    </div>
  </article>

  <div class="bottom-swatch right art"><span class="swatch-name">Lundovia Hearth Plot</span></div>
  <p class="swatch-caption right">The bottom<br>of Ärt &amp; Linsmix bag</p>
</section>

</body>
</html>
```